Veltrano.co - Polar Expeditions Specialists

We need a modern, visually striking business card for Veltrano.co, a company specialized in selling expedition cruises to the most remote regions on Earth, with a focus on the Arctic and Antarctica. The design should instantly communicate that the cardholder is an expert in polar travel. Use clean, premium aesthetics with cool tones like icy blue and white, possibly incorporating polar imagery (ice, glaciers, penguins, etc.)

Attached the logo

Contact Information for Business Card

Feels high-end and trustworthy.. Visually memorable — encourages people to keep it

Colors
0054AA
0677BA
7BADD7
CADEEF
E8F1F8

Requirements
Must have
• ice, glaciers, penguins, montains
Nice to have
• modern, transparente,

```html
<!DOCTYPE html>
<html lang="en">
<head>
<meta charset="utf-8">
<title>Veltrano.co – Business Card</title>
<link href="https://fonts.googleapis.com/css2?family=Poppins:wght@400;500;600;700&display=swap" rel="stylesheet">
<style>
  :root {
    --brand-blue: #2e78b9;
    --ink: #1c1c1c;
    --swoosh: #1a1530;
    --paper: #ffffff;
    --backdrop: #e3e8ea;
  }
  * { margin: 0; padding: 0; box-sizing: border-box; }
  html, body {
    width: 1200px; height: 960px; overflow: hidden;
    background: var(--backdrop);
    font-family: "Poppins", sans-serif;
  }
  .card {
    position: absolute;
    left: 250px;
    width: 701px; height: 400px;
    overflow: hidden;
  }
  .card-front { top: 60px; background: var(--brand-blue); color: var(--paper); }
  .card-back { top: 500px; background: var(--paper); }

  /* Front */
  .front-mark {
    position: absolute; left: 305px; top: 140px;
    width: 90px; height: 90px; border-radius: 50%;
    background: var(--paper);
  }
  .front-name {
    position: absolute; left: 0; right: 0; top: 262px;
    text-align: center; font-weight: 700; font-size: 78px;
    line-height: 1; letter-spacing: 0.5px;
  }
  .front-tagline {
    position: absolute; left: 0; right: 0; top: 360px;
    text-align: center; font-weight: 600; font-size: 22px; line-height: 1;
  }

  /* Back */
  .back-mark {
    position: absolute; left: 182px; top: 36px;
    width: 60px; height: 60px; border-radius: 50%;
    background: var(--brand-blue);
  }
  .back-name {
    position: absolute; left: 271px; top: 36px;
    font-weight: 700; font-size: 50px; line-height: 1;
    color: var(--brand-blue);
  }
  .back-tagline {
    position: absolute; left: 272px; top: 92px;
    font-weight: 600; font-size: 14.5px; line-height: 1;
    color: var(--brand-blue);
  }
  .holder {
    position: absolute; right: 396px; top: 204px; text-align: right;
  }
  .holder-name {
    font-size: 37px; line-height: 1; color: var(--brand-blue); font-weight: 400;
    letter-spacing: 0.5px;
  }
  .holder-name strong { font-weight: 600; }
  .holder-role {
    margin-top: 6px; font-size: 18px; font-weight: 500; color: var(--ink);
    letter-spacing: 0.5px;
  }
  .divider {
    position: absolute; left: 350px; top: 196px;
    width: 1.5px; height: 107px; background: var(--brand-blue);
  }
  .contact-list {
    position: absolute; left: 398px; top: 206px; list-style: none;
  }
  .contact-list li {
    display: flex; align-items: center; gap: 10px;
    height: 25.5px; font-size: 19.5px; color: var(--ink); letter-spacing: 0.3px;
  }
  .contact-list svg { width: 18px; height: 18px; flex: none; }
  .wave { position: absolute; left: 0; top: 0; }
  .address {
    position: absolute; left: 0; right: 0; top: 354px;
    text-align: center; color: var(--paper);
    font-size: 18px; letter-spacing: 0.6px; line-height: 1;
  }
</style>
</head>
<body>

<section class="card card-front">
  <div class="front-mark"></div>
  <h1 class="front-name">Veltrano.co</h1>
  <p class="front-tagline">Polar Expeditions Specialists</p>
</section>

<section class="card card-back">
  <svg class="wave" width="701" height="400" viewBox="0 0 701 400" aria-hidden="true">
    <path d="M0 282 Q350.5 412 701 282 L701 400 L0 400 Z" fill="var(--brand-blue)"/>
    <path d="M26 282 Q350 394 677 282 Q350 380 26 282 Z" fill="var(--swoosh)"/>
  </svg>

  <div class="back-mark"></div>
  <h2 class="back-name">Veltrano.co</h2>
  <p class="back-tagline">Polar Expeditions Specialists</p>

  <div class="holder">
    <p class="holder-name"><strong>Mira</strong> Kovanda</p>
    <p class="holder-role">Founder &amp; CEO</p>
  </div>

  <div class="divider"></div>

  <ul class="contact-list">
    <li>
      <svg viewBox="0 0 24 24" aria-hidden="true"><path fill="var(--brand-blue)" d="M6.6 10.8a15.1 15.1 0 0 0 6.6 6.6l2.2-2.2c.3-.3.7-.4 1-.2 1.1.4 2.3.6 3.6.6.6 0 1 .4 1 1V20c0 .6-.4 1-1 1A17 17 0 0 1 3 4c0-.6.4-1 1-1h3.5c.6 0 1 .4 1 1 0 1.3.2 2.5.6 3.6.1.3 0 .7-.2 1z"/></svg>
      <span>(555) 014-2290</span>
    </li>
    <li>
      <svg viewBox="0 0 24 24" aria-hidden="true"><circle cx="12" cy="12" r="9.5" fill="none" stroke="var(--brand-blue)" stroke-width="2"/><path d="M2.5 12h19M12 2.5c3 3 3 16 0 19M12 2.5c-3 3-3 16 0 19" fill="none" stroke="var(--brand-blue)" stroke-width="1.6"/></svg>
      <span>info@yourwebsite.com</span>
    </li>
    <li>
      <svg viewBox="0 0 24 24" aria-hidden="true"><rect x="2" y="6" width="20" height="15" rx="1.5" fill="none" stroke="var(--brand-blue)" stroke-width="2"/><path d="M2.5 7l9.5 7 9.5-7" fill="none" stroke="var(--brand-blue)" stroke-width="2"/></svg>
      <span>www.yourwebsite.com</span>
    </li>
  </ul>

  <p class="address">418 Harbor Lane Suite 300 Seattle, WA 98101</p>
</section>

</body>
</html>
```